New Innovative Counselling and psychotherapy Service needs Business Card design

Keep it simple and professional. On one side, just company name and logo (perhaps in all blue) and maybe a tag line.

On other side (all white) my name and Qualifications in centre

Industry/Entity Type

Health And Wellness

Contact Information for Business Card

Dara Whelby
Counsellor & Psychotherapist
BSc (Psychol.), BA, Dip. (Couns. & Psych.), PG.Cert (CBT), FGTrK, ONRE

I will also require Mobile no, Email and web site address of which I'll pass on to final designer.

Font styles to use
Sans Serif

Requirements
Must have
• My Logo Only and please use the colours in logo that is in it.
Should not have
• Any other images

```html
<!DOCTYPE html>
<html lang="en">
<head>
<meta charset="utf-8">
<title>Northfield Lane – Business Card</title>
<link rel="stylesheet" href="https://fonts.googleapis.com/css2?family=Open+Sans:ital,wght@0,300;0,400;0,600;0,700;1,400&display=swap">
<style>
  :root {
    --backdrop: #3b332f;
    --card: #141414;
    --card-edge: #1d1d1d;
    --brand-blue: #3ba3e3;
    --brand-green: #7cc242;
    --text-light: #f2f2f2;
    --text-muted: #9a9a9a;
    --divider: #5a5a5a;
    --mark-tone: #232323;
  }
  * { box-sizing: border-box; margin: 0; padding: 0; }
  html, body {
    width: 1200px; height: 864px; overflow: hidden;
    background: var(--backdrop);
    font-family: "Open Sans", Arial, sans-serif;
  }
  .canvas {
    width: 1200px; height: 864px;
    display: flex; align-items: center; justify-content: center; gap: 40px;
  }
  .card {
    width: 540px; height: 309px;
    background: var(--card);
    border: 1px solid var(--card-edge);
    border-radius: 3px;
    position: relative;
    box-shadow: 0 10px 30px rgba(0,0,0,.45);
  }

  /* Reverse side */
  .card-back { display: flex; flex-direction: column; align-items: center; justify-content: center; }
  .back-mark {
    width: 120px; height: 120px; border-radius: 50%;
    background: var(--mark-tone);
    margin-bottom: 26px;
  }
  .back-tagline {
    font-style: italic; font-size: 13px; color: var(--text-muted); letter-spacing: .2px;
  }

  /* Contact side */
  .card-front { display: flex; align-items: center; }
  .brand {
    width: 238px; display: flex; align-items: center; justify-content: center; gap: 8px;
  }
  .brand-dot { width: 20px; height: 20px; border-radius: 50%; background: var(--brand-blue); }
  .brand-name { font-size: 19px; font-weight: 400; color: var(--text-light); }
  .divider { width: 1px; height: 150px; background: var(--divider); }
  .details { padding-left: 24px; }
  .person-name { font-size: 17px; font-weight: 700; color: var(--brand-blue); line-height: 1.1; text-transform: uppercase; }
  .person-role { font-size: 15px; font-weight: 400; color: var(--brand-green); text-transform: uppercase; line-height: 1.3; }
  .person-quals { font-size: 9.5px; color: var(--brand-green); line-height: 1.35; margin-bottom: 10px; }
  .contact-list { list-style: none; }
  .contact-list li {
    display: flex; align-items: center; gap: 8px;
    font-size: 13px; color: var(--text-light); line-height: 1.45;
  }
  .contact-list svg { width: 11px; height: 11px; flex: none; }
</style>
</head>
<body>
<main class="canvas">
  <section class="card card-back" aria-label="Card reverse">
    <div class="back-mark"></div>
    <p class="back-tagline">Caring For Your Psychological Well-Being Is Our Top Priority</p>
  </section>

  <section class="card card-front" aria-label="Card contact side">
    <div class="brand">
      <span class="brand-dot"></span>
      <span class="brand-name">Northfield Lane</span>
    </div>
    <div class="divider"></div>
    <div class="details">
      <h1 class="person-name">Dara Whelby</h1>
      <p class="person-role">Counsellor &amp; Psychotherapist</p>
      <p class="person-quals">BSc (Psychol.), BA, Dip. (Couns. &amp; Psych.),<br>PG.Cert (CBT), FGTrK,</p>
      <ul class="contact-list">
        <li>
          <svg viewBox="0 0 12 12" aria-hidden="true"><rect x="3" y="0.5" width="6" height="11" rx="1" fill="none" stroke="#3ba3e3" stroke-width="1.2"/><circle cx="6" cy="9.5" r=".7" fill="#3ba3e3"/></svg>
          555 201 7480
        </li>
        <li>
          <svg viewBox="0 0 12 12" aria-hidden="true"><rect x=".5" y="2" width="11" height="8" fill="#3ba3e3"/><path d="M.5 2 6 6.5 11.5 2" fill="none" stroke="#141414" stroke-width="1"/></svg>
          dara@northfieldlane.com
        </li>
        <li>
          <svg viewBox="0 0 12 12" aria-hidden="true"><circle cx="6" cy="6" r="5.5" fill="#3ba3e3"/><path d="M.5 6h11M6 .5c-2.5 3-2.5 8 0 11M6 .5c2.5 3 2.5 8 0 11" fill="none" stroke="#141414" stroke-width=".8"/></svg>
          www.northfieldlane.com
        </li>
      </ul>
    </div>
  </section>
</main>
</body>
</html>
```